Clean Modern Skin Product branding/ label.

I need a label for a skincare line. The company is Dermaloft but product names will vary. A couple products to list are:
Sensitive Cleanser, Lumeno, Repair, Halo up, Mendora, Mendora Plus, Mendora Intense, Tavelo, Balance and Vivanto.

I would like the color scheme to be muted greens, grays, tourquise. The bottles are white, boston shaped with pumps, and ounces are 2, 4, 8, 16 ounces. When I choose the design, I can give you exact label sizes. Along with the ingredience already on the product label.

The look I desire is clean, minimal. A modern, organic look. Ideas that come to mind are a Veloraine,https://www.veloraine-example.com/product/2846/37204/3-step/step-2-exfoliate/clarifying-lotion-1 and the simplicity of Bo Tarn.

Both styles high light the name, in this case Dermaloft, and then the specific product.

My product is clean utilizing pure ingredients rather that a bunch fillers and binders. When I work with my clients I normally will say we need to "restore the balance" from over use of harsh products. That is why this lines works. It restores the skin to it's natural state. The process is simple, so I would like the label to reflect that simplicity.

Target Market(s)

Anyone with sensitive skin. So gender neutral

Industry/Entity Type

Skin Care Product

Font styles to use
Serif
Sans Serif
Decorative

Colors
acd037
33b8a4
fcfefd
85cae6
d3d3d3

Requirements
Must have
• Logo, name of product and color identity for cleanser, Active products, moisturizers
• I am thinking we could have one color for a cleanser and a space where I can put a sticker on which cleanser it is. Acne Cleasner, Sensitive Cleanser, and Cleanser.
Nice to have
• Not sure....suprise me. I would like the font to stay the same on the DERMALOFT, but you can change color, or color of leaf.
Should not have
• Too busy, too crowded or look like every other skincare line

```html
<!DOCTYPE html>
<html lang="en">
<head>
<meta charset="utf-8">
<title>Dermaloft – Sensitive Cleanser Label</title>
<link rel="stylesheet" href="https://fonts.googleapis.com/css2?family=Comfortaa:wght@300;600&family=Roboto:wght@300&display=swap">
<style>
  :root {
    --backdrop: #b3e25a;
    --label-white: #ffffff;
    --brand-green: #568a2d;
    --product-slate: #3f5c6e;
    --rule-slate: #5d7585;
    --leaf-green: #5cd41c;
    --tagline-green: #52d81a;
  }
  * { box-sizing: border-box; margin: 0; padding: 0; }
  html, body {
    width: 1200px;
    height: 1200px;
    overflow: hidden;
    background: var(--backdrop);
  }
  .canvas {
    position: relative;
    width: 1200px;
    height: 1200px;
  }
  .label {
    position: absolute;
    left: 130px;
    top: 62px;
    width: 940px;
    height: 1076px;
    background: var(--label-white);
    box-shadow: 0 4px 14px rgba(40, 70, 10, 0.25);
  }
  .brand-name {
    position: absolute;
    left: 0;
    top: 186px;
    width: 100%;
    text-align: center;
    font-family: "Comfortaa", sans-serif;
    font-weight: 600;
    font-size: 118px;
    line-height: 1;
    letter-spacing: -2px;
    color: var(--brand-green);
    white-space: nowrap;
  }
  .product-name {
    position: absolute;
    left: 197px;
    top: 398px;
    width: 546px;
    height: 76px;
    border-top: 1.5px solid var(--rule-slate);
    border-bottom: 1.5px solid var(--rule-slate);
    text-align: center;
    font-family: "Roboto", sans-serif;
    font-weight: 300;
    font-size: 62px;
    line-height: 72px;
    color: var(--product-slate);
    white-space: nowrap;
  }
  .accent-mark {
    position: absolute;
    left: 410px;
    top: 800px;
    width: 120px;
    height: 120px;
    border-radius: 50%;
    background: var(--leaf-green);
  }
  .tagline {
    position: absolute;
    left: 0;
    top: 945px;
    width: 100%;
    text-align: center;
    font-family: "Comfortaa", sans-serif;
    font-weight: 300;
    font-size: 50px;
    line-height: 1.2;
    color: var(--tagline-green);
    white-space: nowrap;
  }
</style>
</head>
<body>
  <main class="canvas">
    <section class="label">
      <h1 class="brand-name">Dermaloft</h1>
      <h2 class="product-name">Sensitive Cleanser</h2>
      <div class="accent-mark" role="img" aria-label="Small green leaf emblem above the tagline"></div>
      <p class="tagline">restore the balance</p>
    </section>
  </main>
</body>
</html>
```